Beacon Advisory Website

I currently have a website www.beaconadvisoryinc.com. We are a IT Consulting Company. Our website will pretty much tell out our services. I am looking to enhance my website and make it look more professional. Looking for very classy and Contemporary look and design for my website.

It Company

```html
<!DOCTYPE html>
<html lang="en">
<head>
<meta charset="utf-8">
<title>Beacon Advisory</title>
<link href="https://fonts.googleapis.com/css2?family=Raleway:wght@300;400;500;700&family=Open+Sans:wght@400;600&display=swap" rel="stylesheet">
<style>
:root{
  --blue:#1ba1e2;
  --blue-dark:#0d86c4;
  --ink:#222;
  --grey:#666;
  --light:#f3f4f6;
  --dark:#2b2c2e;
  --white:#fff;
  --black:#111;
}
*{box-sizing:border-box;margin:0;padding:0}
html,body{width:1200px;height:3974px;overflow:hidden;background:var(--white)}
body{font-family:"Open Sans",Arial,sans-serif;color:var(--ink);position:relative}
.canvas{position:relative;width:1200px;height:3974px;overflow:hidden}
section,header,nav,footer{position:absolute;left:0;width:1200px}
.h-title{font-family:"Raleway",Arial,sans-serif;font-weight:300;letter-spacing:1px}

/* top bar */
.topbar{top:0;height:58px;background:var(--blue);color:var(--white);z-index:2}
.social{position:absolute;left:80px;top:12px;display:flex;gap:28px}
.social span{width:34px;height:34px;border-radius:50%;border:2px solid rgba(255,255,255,.8);display:block}
.social span+span{border:none;background:rgba(255,255,255,.25)}
.contact{position:absolute;right:80px;top:18px;display:flex;gap:30px;font-size:15px;align-items:center}
.contact div{display:flex;align-items:center;gap:10px}

/* nav */
.nav{top:58px;height:120px;background:var(--white);z-index:1}
.brand{position:absolute;left:80px;top:42px;display:flex;align-items:center;gap:10px;font-family:"Raleway",Arial,sans-serif;font-weight:700;font-size:23px;color:var(--blue-dark);letter-spacing:.5px;white-space:nowrap}
.brand i{width:36px;height:36px;background:var(--blue-dark);display:block;flex:none}
.menu{position:absolute;right:78px;top:50px;display:flex;gap:34px;font-family:"Raleway",Arial,sans-serif;font-size:16px;color:#555;text-transform:uppercase;white-space:nowrap}
.menu .active{color:var(--blue);position:relative}
.menu .active::after{content:"";position:absolute;left:50%;top:30px;margin-left:-8px;border:8px solid transparent;border-top-color:var(--blue)}

/* hero */
.hero{top:178px;height:678px}
.hero-photo{position:absolute;inset:0;background:linear-gradient(100deg,#3f4145 0%,#8a8d91 45%,#bfc2c6 70%,#5d6065 100%)}
.hero-text{position:absolute;left:80px;top:222px;color:var(--white)}
.hero-text h1{font-family:"Raleway",Arial,sans-serif;font-weight:400;font-size:58px;letter-spacing:1px}
.hero-text p{font-family:"Raleway",Arial,sans-serif;font-size:25px;margin-top:10px;line-height:1.35;width:540px}
.btn{display:inline-block;font-family:"Raleway",Arial,sans-serif;font-size:20px;text-transform:uppercase;padding:18px 24px;letter-spacing:.5px}
.btn-white{background:var(--white);color:var(--blue);margin-top:30px}
.btn-blue{background:var(--blue);color:var(--white);box-shadow:0 3px 6px rgba(0,0,0,.25)}
.btn-black{background:var(--black);color:var(--white)}

/* welcome */
.welcome{top:856px;height:416px;text-align:center;background:linear-gradient(135deg,#fff 0%,#f2f3f5 50%,#fff 100%)}
.welcome .eyebrow{font-family:"Raleway",Arial,sans-serif;color:var(--blue);font-size:20px;margin-top:62px}
.welcome h2{color:var(--blue);font-size:44px;margin-top:10px}
.welcome p{width:900px;margin:26px auto 0;font-size:15.5px;line-height:1.85;color:var(--grey)}
.welcome .btn{margin-top:28px}

/* what we do */
.whatwedo{top:1272px;height:533px;background:linear-gradient(180deg,#3a3b3e 0%,#2a2b2d 100%);color:var(--white);text-align:center}
.whatwedo h2{font-size:42px;margin-top:58px}
.wwd-cols{position:absolute;top:148px;left:0;width:1200px}
.wwd-item{position:absolute;width:300px;text-align:center}
.wwd-icon{width:122px;height:122px;border-radius:50%;border:3px solid var(--white);margin:0 auto;display:flex;align-items:center;justify-content:center}
.wwd-icon div{width:100px;height:100px;border-radius:50%}
.wwd-item h3{font-family:"Raleway",Arial,sans-serif;font-weight:400;font-size:20px;margin-top:28px;letter-spacing:.5px}
.wwd-item p{font-size:14.5px;line-height:1.75;margin-top:16px;color:#ddd}
.wwd-item a{display:block;color:var(--blue);font-size:14.5px;margin-top:16px;text-decoration:none;text-transform:uppercase}

/* services */
.services{top:1805px;height:625px;background:var(--blue);color:var(--white)}
.services h2{text-align:center;font-size:42px;margin-top:56px}
.svc-grid{position:absolute;left:80px;top:140px;display:flex;gap:15px}
.svc{width:250px}
.svc-photo{height:167px;background:linear-gradient(135deg,#dfe5ea,#a9b6c1)}
.svc h3{font-family:"Raleway",Arial,sans-serif;font-weight:500;font-size:20px;margin-top:30px;text-transform:uppercase}
.svc p{font-size:13.5px;line-height:1.7;margin-top:14px;white-space:nowrap;overflow:hidden}
.svc a{display:block;color:var(--black);font-size:14px;font-style:italic;text-decoration:underline;margin-top:12px}
.services .btn{position:absolute;left:512px;top:500px;padding:18px 32px}

/* news */
.news{top:2430px;height:551px;background:linear-gradient(135deg,#f7f7f8 0%,#eceef0 50%,#f8f8f9 100%);text-align:center}
.news h2{color:var(--blue);font-size:42px;font-weight:500;margin-top:56px;letter-spacing:2px}
.news .sub{color:var(--grey);font-size:19px;margin-top:14px}
.news-grid{position:absolute;left:80px;top:188px;display:flex;gap:15px;text-align:left}
.post{width:250px}
.post .date{font-family:"Raleway",Arial,sans-serif;font-size:54px;color:#777;font-weight:300}
.post .date span{font-size:22px;margin-left:6px}
.post h3{font-family:"Raleway",Arial,sans-serif;font-weight:500;font-size:21px;margin-top:10px}
.post p{font-size:13.5px;line-height:1.8;margin-top:18px;color:#555}
.post.featured .date,.post.featured h3,.post.featured p{color:var(--blue)}
.news .btn{position:absolute;left:512px;top:422px;padding:18px 32px}

/* clients */
.clients{top:2981px;height:411px;background:var(--white);text-align:center}
.clients h2{color:var(--blue);font-size:42px;margin-top:50px}
.clients .sub{color:#555;font-size:19px;margin-top:8px}
.quote{position:absolute;top:178px;width:470px;display:flex;gap:22px;text-align:left}
.avatar{width:143px;height:143px;border-radius:50%;border:4px solid #eee;box-shadow:0 2px 5px rgba(0,0,0,.25);background:linear-gradient(135deg,#d9c2b0,#8a6f5c);flex:none}
.quote-body{padding-top:14px;font-size:15px;line-height:1.75;color:#555;position:relative}
.quote-body .qm{color:var(--blue);font-family:Georgia,serif;font-size:44px;line-height:.5;vertical-align:-12px;margin-right:4px}
.quote-body a{display:block;margin-top:8px;color:var(--blue);font-weight:600;font-size:15px;text-decoration:underline}

/* map */
.map{top:3392px;height:519px}
.map-fill{position:absolute;inset:0;background:linear-gradient(135deg,#e8e6e1 0%,#dedcd6 50%,#e9e7e2 100%)}
.map-search{position:absolute;left:12px;top:6px;width:480px;height:58px;background:var(--white);box-shadow:0 1px 4px rgba(0,0,0,.3);font-size:20px;padding:16px 22px;color:#222}
.offices{position:absolute;left:212px;top:128px;width:782px;height:222px;background:rgba(255,255,255,.72);display:flex;padding:30px 52px;gap:40px}
.office{width:220px}
.office h4{font-family:"Raleway",Arial,sans-serif;font-weight:500;color:var(--blue);font-size:16px;text-transform:uppercase}
.office p{font-size:13.5px;line-height:1.75;color:#444;margin-top:14px}

/* footer */
.footer{top:3911px;height:63px;background:var(--black);color:var(--white);text-align:center;font-size:14px;line-height:63px}
.footer b{color:var(--blue);font-weight:400}
</style>
</head>
<body>
<div class="canvas">

<header class="topbar">
  <div class="social" aria-label="Social links"><span></span><span></span><span></span></div>
  <div class="contact">
    <div>
      <svg width="20" height="20" viewBox="0 0 24 24"><path fill="#fff" d="M6.6 10.8a15 15 0 0 0 6.6 6.6l2.2-2.2c.3-.3.7-.4 1-.2 1.1.4 2.3.6 3.6.6.6 0 1 .4 1 1V20c0 .6-.4 1-1 1A17 17 0 0 1 3 4c0-.6.4-1 1-1h3.5c.6 0 1 .4 1 1 0 1.3.2 2.5.6 3.6.1.3 0 .7-.2 1z"/></svg>
      +1 (555) 014 2290 FREE
    </div>
    <div>
      <svg width="24" height="18" viewBox="0 0 24 18"><rect width="24" height="18" rx="2" fill="#fff"/><path d="M1 2l11 8 11-8" stroke="#1ba1e2" stroke-width="2" fill="none"/></svg>
      Mail id: careers@beaconadvisoryinc.com
    </div>
  </div>
</header>

<nav class="nav">
  <div class="brand"><i></i>BEACON ADVISORY</div>
  <div class="menu">
    <span class="active">Company</span><span>Services</span><span>Solution</span><span>Resources</span><span>Career</span><span>Contact Us</span>
  </div>
</nav>

<section class="hero">
  <div class="hero-photo" role="img" aria-label="Smiling consultant in a dark suit with arms crossed, standing in a glass office atrium"></div>
  <div class="hero-text">
    <h1>BEACON ADVISORY</h1>
    <p>We provide unique and tailored solutions for various industries!</p>
    <span class="btn btn-white">Contact Now</span>
  </div>
</section>

<section class="welcome">
  <div class="eyebrow">WELCOME TO</div>
  <h2 class="h-title">BEACON ADVISORY</h2>
  <p>Today's IT market is a dynamic, fast-paced industry, with ever-increasing demands. Meeting these demands for over 25 years, Beacon Advisory maintains a global presence, aggressively recruiting expertly qualified IT and Management Professionals from around the world and cultivating key partnerships with corporations to understand their business models end-to-end, with a goal of delivering exceptional client service and ensuring a consistent delivery of the talent needed to drive results...</p>
  <span class="btn btn-blue">Know More</span>
</section>

<section class="whatwedo">
  <h2 class="h-title">WHAT WE DO</h2>
  <div class="wwd-cols">
    <div class="wwd-item" style="left:88px">
      <div class="wwd-icon"><div style="background:var(--blue)" role="img" aria-label="Consulting team icon"></div></div>
      <h3>CONSULTING</h3>
      <p>Beacon Advisory has certified professional consultants to work with you to help increase the business by ...</p>
      <a>Read More</a>
    </div>
    <div class="wwd-item" style="left:450px">
      <div class="wwd-icon"><div style="background:var(--white)" role="img" aria-label="Staff network icon"></div></div>
      <h3>STAFF AUGMENTION</h3>
      <p>For years Beacon Advisory as been offering our customers the ability to augment their existing staff ...</p>
      <a>Read More</a>
    </div>
    <div class="wwd-item" style="left:810px">
      <div class="wwd-icon"><div style="background:var(--white)" role="img" aria-label="Light bulb idea icon"></div></div>
      <h3>OFFSHORE</h3>
      <p>Our Offshore development model has a unique distinction of providing efficient software solutions...</p>
      <a>Read More</a>
    </div>
  </div>
</section>

<section class="services">
  <h2 class="h-title">OUR SERVICES</h2>
  <div class="svc-grid">
    <div class="svc">
      <div class="svc-photo" role="img" aria-label="Businesswoman holding a globe" style="background:linear-gradient(135deg,#6f7378,#2f3236)"></div>
      <h3>Technology</h3>
      <p>Beacon Advisory Training programs<br>are perfect for individuals to enhance</p>
      <a>READ MORE</a>
    </div>
    <div class="svc">
      <div class="svc-photo" role="img" aria-label="Woman working at a bright office desk"></div>
      <h3>Development</h3>
      <p>Beacon Advisory Training programs<br>are perfect for individuals to enhance</p>
      <a>READ MORE</a>
    </div>
    <div class="svc">
      <div class="svc-photo" role="img" aria-label="Group of business professionals standing together" style="background:linear-gradient(135deg,#e6e8ea,#8f99a3)"></div>
      <h3>IT Consulting</h3>
      <p>Beacon Advisory Training programs<br>are perfect for individuals to enhance</p>
      <a>READ MORE</a>
    </div>
    <div class="svc">
      <div class="svc-photo" role="img" aria-label="Team meeting around a conference table" style="background:linear-gradient(135deg,#f2f3f4,#9aa3ab)"></div>
      <h3>Business</h3>
      <p>Beacon Advisory Training programs<br>are perfect for individuals to enhance</p>
      <a>READ MORE</a>
    </div>
  </div>
  <span class="btn btn-black">Show All</span>
</section>

<section class="news">
  <h2 class="h-title">LATEST NEWS</h2>
  <div class="sub">Lorem ipsum dolor sit amet Lorem ipsum dolor sit amet</div>
  <div class="news-grid">
    <div class="post featured"><div class="date">01<span>March</span></div><h3>Lorem ipsum dolor</h3><p>Lorem ipsum dolor sit amet, Lorem consectetur adipiscing elit dolor...</p></div>
    <div class="post"><div class="date">02<span>March</span></div><h3>Lorem ipsum dolor</h3><p>Lorem ipsum dolor sit amet, Lorem consectetur adipiscing elit dolor...</p></div>
    <div class="post"><div class="date">03<span>March</span></div><h3>Lorem ipsum dolor</h3><p>Lorem ipsum dolor sit amet, Lorem consectetur adipiscing elit dolor...</p></div>
    <div class="post"><div class="date">04<span>March</span></div><h3>Lorem ipsum dolor</h3><p>Lorem ipsum dolor sit amet, Lorem consectetur adipiscing elitdolor...</p></div>
  </div>
  <span class="btn btn-blue">Show All</span>
</section>

<section class="clients">
  <h2 class="h-title">PORTFOLIO CLIENTS</h2>
  <div class="sub">What Our Client say</div>
  <div class="quote" style="left:80px">
    <div class="avatar" role="img" aria-label="Client portrait"></div>
    <div class="quote-body"><span class="qm">&ldquo;</span>Lorem ipsum dolor sit amet, consectetur adipiscing elit. Aenean feugiat dictum lacusLorem ipsum d <span class="qm">&rdquo;</span><a>CLIENT NAME</a></div>
  </div>
  <div class="quote" style="left:615px">
    <div class="avatar" role="img" aria-label="Client portrait" style="background:linear-gradient(135deg,#e0c9b6,#7d6251)"></div>
    <div class="quote-body"><span class="qm">&ldquo;</span>Lorem ipsum dolor sit amet, consectetur adipiscing elit. Aenean feugiat dictum lacusLorem ipsum d <span class="qm">&rdquo;</span><a>CLIENT NAME</a></div>
  </div>
</section>

<section class="map">
  <div class="map-fill" role="img" aria-label="Street map around the head office location"></div>
  <div class="map-search">420 Harbor Ave &nbsp;&nbsp; Suite 205</div>
  <div class="offices">
    <div class="office"><h4>Head Office</h4><p>420 Harbor Ave<br>Suite 205<br>Westfield, NJ 07090<br>Phone: +1 (555) 014 2290 FREE</p></div>
    <div class="office"><h4>Technical Center</h4><p>1800 Linden Road<br>Suite 255<br>Oakbrook MI 48300</p></div>
    <div class="office"><h4>West Cost Office</h4><p>75 Meridian Place<br>Suite 500<br>Riverton, CA 95100</p></div>
  </div>
</section>

<footer class="footer">© 2016. <b>BEACON ADVISORY</b> All Rights Reserved.</footer>

</div>
</body>
</html>
```